Business Card Design

We are a manufacturing and distribution company with most of our customer base being supermarkets. We have established brand guidelines that are attached.

```html
<!DOCTYPE html>
<html lang="en">
<head>
<meta charset="utf-8">
<title>Velorano Business Card</title>
<link rel="stylesheet" href="https://fonts.googleapis.com/css2?family=Montserrat:wght@700;800&family=Roboto:wght@400&display=swap">
<style>
  :root {
    --page-bg: #e9e7e6;
    --card-dark: #231f20;
    --accent-red: #e31e24;
    --accent-blue: #0f6bb5;
    --text-light: #ffffff;
    --brand-ink: #231f20;
    --frost-light: #f7f5f5;
    --frost-mid: #dcd6d6;
  }
  html, body {
    margin: 0;
    padding: 0;
    width: 1200px;
    height: 900px;
    overflow: hidden;
    background: var(--page-bg);
  }
  .business-card {
    position: absolute;
    left: 100px;
    top: 140px;
    width: 1000px;
    height: 620px;
    overflow: hidden;
    box-shadow: 0 10px 30px rgba(0,0,0,0.18);
    background: linear-gradient(160deg, var(--frost-light) 0%, #ece6e6 45%, var(--frost-mid) 100%);
  }
  .card-shapes {
    position: absolute;
    inset: 0;
  }
  .contact-panel {
    position: absolute;
    left: 60px;
    top: 0;
    color: var(--text-light);
    font-family: "Roboto", Arial, sans-serif;
  }
  .person-name {
    position: absolute;
    top: 114px;
    margin: 0;
    white-space: nowrap;
    font-family: "Montserrat", Arial, sans-serif;
    font-weight: 700;
    font-size: 44px;
    letter-spacing: 0.5px;
    line-height: 1;
  }
  .person-name .first-name { color: var(--accent-red); }
  .person-name .last-name { color: var(--accent-blue); }
  .person-title {
    position: absolute;
    top: 165px;
    margin: 0;
    white-space: nowrap;
    font-size: 28px;
  }
  .postal-address {
    position: absolute;
    top: 250px;
    margin: 0;
    font-style: normal;
    white-space: nowrap;
    font-size: 28px;
    line-height: 37px;
  }
  .contact-list {
    position: absolute;
    top: 396px;
    margin: 0;
    padding: 0;
    list-style: none;
    font-size: 28px;
    line-height: 37px;
    white-space: nowrap;
  }
  .contact-item {
    display: flex;
    align-items: center;
    gap: 8px;
  }
  .contact-icon {
    width: 26px;
    height: 26px;
    flex: none;
  }
  .brand-name {
    position: absolute;
    left: 533px;
    top: 322px;
    width: 410px;
    margin: 0;
    text-align: center;
    font-family: "Montserrat", Arial, sans-serif;
    font-weight: 800;
    font-size: 66px;
    letter-spacing: 2px;
    color: var(--brand-ink);
    line-height: 1;
  }
</style>
</head>
<body>
  <section class="business-card">
    <svg class="card-shapes" width="1000" height="620" viewBox="0 0 1000 620" aria-hidden="true">
      <polygon class="dark-panel" points="0,0 597,0 384,302 556,620 0,620" fill="var(--card-dark)"/>
      <line class="edge-red" x1="600" y1="0" x2="384" y2="302" stroke="var(--accent-red)" stroke-width="5"/>
      <line class="edge-blue" x1="384" y1="302" x2="557" y2="620" stroke="var(--accent-blue)" stroke-width="5"/>
    </svg>

    <div class="contact-panel">
      <h1 class="person-name"><span class="first-name">DANIEL</span> <span class="last-name">HARPER</span></h1>
      <p class="person-title">Managing Director</p>

      <address class="postal-address">18, Harbour Works Road<br>Eastfield<br>20417,Northland</address>

      <ul class="contact-list">
        <li class="contact-item">
          <svg class="contact-icon" viewBox="0 0 24 24" aria-hidden="true">
            <path d="M6.6 10.8a15.1 15.1 0 0 0 6.6 6.6l2.2-2.2a1 1 0 0 1 1-.25 11.4 11.4 0 0 0 3.6.57 1 1 0 0 1 1 1V20a1 1 0 0 1-1 1A17 17 0 0 1 3 4a1 1 0 0 1 1-1h3.5a1 1 0 0 1 1 1c0 1.25.2 2.45.57 3.57a1 1 0 0 1-.25 1z" fill="var(--accent-red)"/>
            <path d="M14 3a7 7 0 0 1 7 7M14 6.5A3.5 3.5 0 0 1 17.5 10" stroke="var(--accent-red)" stroke-width="1.8" fill="none"/>
          </svg>
          <span>044-987 321 654</span>
        </li>
        <li class="contact-item">
          <svg class="contact-icon" viewBox="0 0 24 24" aria-hidden="true">
            <rect x="1" y="5" width="22" height="14" fill="var(--accent-red)"/>
            <path d="M1 5l11 8 11-8" stroke="var(--card-dark)" stroke-width="1.6" fill="none"/>
          </svg>
          <span>hello@velorano.com</span>
        </li>
        <li class="contact-item">
          <svg class="contact-icon" viewBox="0 0 24 24" aria-hidden="true">
            <g stroke="var(--accent-red)" stroke-width="1.8" fill="none">
              <circle cx="12" cy="12" r="10"/>
              <ellipse cx="12" cy="12" rx="4.5" ry="10"/>
              <line x1="2" y1="12" x2="22" y2="12"/>
              <line x1="12" y1="2" x2="12" y2="22"/>
            </g>
          </svg>
          <span>www.velorano.com</span>
        </li>
      </ul>
    </div>

    <p class="brand-name">VELORANO</p>
  </section>
</body>
</html>
```